The Marigold Venture WEBSITE DESIGN

Marigold is a not for profit working in international aid and development. The website needs to be lively not depressing,earthy rather than bling, have a dramatic impact over lightweight. It may be that a black and white with spot colour may be more impacting given the simplicity I want for the site. Marigold works in partnership with registered NGOs in Asia and Africa. At any one time it will have about five feature projects. The purpose is for people to be able to find out about the projects, the countries, the partner organisations, people's stories and then give people the opportunity to give their financial and volunteer support.

Target Market(s)

First World Donors
All ages but particularly 25 - 55

Industry/Entity Type

Human Rights

Number of Pages Required

5+ page

Font styles to use
Sans Serif

Requirements
Must have
• Simplicity
• Easy access to giving options
• Highlight stories both video and image + copy (sample in attachments)
• Lots of images over copy
Nice to have
• Interest
• Not boring
• May work in black and white with a spot colour or sepia look
Should not have
• Shiny new look
• Dont know how many pages or if it be coded or uncoded - makes no sense to me

```html
<!DOCTYPE html>
<html lang="en">
<head>
<meta charset="utf-8">
<title>The Marigold Venture</title>
<link href="https://fonts.googleapis.com/css2?family=Lato:wght@300;400;700;900&display=swap" rel="stylesheet">
<style>
:root{
  --orange:#f39422;
  --teal:#86cfc9;
  --teal-dark:#5fb7b0;
  --blue:#2f86c6;
  --ink:#3a3a3a;
  --muted:#777;
  --line:#e3e3e3;
  --footer:#2c2c2c;
  --footer-deep:#1f1f1f;
  --white:#fff;
}
*{box-sizing:border-box;margin:0;padding:0}
html,body{width:702px;height:1200px;overflow:hidden;background:var(--white)}
body{font-family:"Lato",sans-serif;color:var(--ink);font-size:9px;line-height:1.45}
.page{width:702px;height:1200px;position:relative}

/* header */
.site-header{height:70px;position:relative;background:var(--white)}
.topbar{display:flex;justify-content:space-between;align-items:center;padding:8px 26px 0}
.topbar .phone{display:flex;align-items:center;gap:5px;color:var(--muted);font-size:8.5px}
.social{display:flex;gap:5px}
.social span{width:13px;height:13px;border-radius:50%;display:block}
.s1{background:#3b5998}.s2{background:#35a9e0}.s3{background:#d64136}.s4{background:#444}
.nav{display:flex;align-items:center;justify-content:space-between;padding:10px 26px 0;font-size:8.5px;font-weight:700;letter-spacing:.3px;text-transform:uppercase}
.nav ul{display:flex;gap:20px;list-style:none}
.nav li.active{color:var(--orange)}
.brand{position:absolute;left:50%;top:4px;transform:translateX(-50%);display:flex;flex-direction:column;align-items:center;gap:3px}
.brand .mark{width:30px;height:30px;border-radius:50%;background:var(--orange)}
.brand .name{font-weight:900;font-size:13px;color:var(--orange);letter-spacing:1px;line-height:1.05;text-align:center}

/* hero */
.hero{height:295px;position:relative;background:linear-gradient(100deg,#d9c9b4 0%,#c98f94 30%,#d7436f 55%,#b9a597 80%,#e6dccf 100%)}
.hero-copy{position:absolute;left:76px;top:100px}
.hero-copy .line{display:inline-block;color:var(--white);font-size:16px;font-weight:400;padding:3px 8px;margin-bottom:6px}
.line-a{background:rgba(243,148,34,.8)}
.line-b{background:var(--orange)}
.btn{display:inline-block;background:var(--blue);color:var(--white);font-weight:700;font-size:8px;padding:5px 11px;border-radius:2px;text-transform:uppercase}

/* welcome */
.welcome{display:flex;justify-content:space-between;padding:22px 76px 0;height:206px}
.welcome-text{width:322px}
.section-title{display:flex;align-items:center;gap:8px;font-size:17px;font-weight:400;text-transform:uppercase;color:var(--ink);margin-bottom:8px}
.section-title em{font-style:normal;color:var(--orange)}
.title-icon{width:16px;height:16px;border-radius:50%;border:3px solid var(--orange);flex:none}
.welcome-text p{color:var(--muted);margin-bottom:10px}
.welcome-text p.lead{color:var(--ink);font-weight:700}
.video{width:202px;height:130px;margin-top:12px;position:relative;background:linear-gradient(160deg,#e9eef0,#b7c6cd)}
.video-bar{position:absolute;left:0;right:0;bottom:0;height:16px;background:rgba(0,0,0,.75);display:flex;align-items:center;padding:0 6px;gap:6px}
.video-bar .track{flex:1;height:3px;background:#777}
.video-bar .track i{display:block;width:30%;height:3px;background:var(--white)}

/* projects */
.projects{background:var(--teal);height:242px;text-align:center;padding-top:16px}
.band-title{color:var(--white);font-size:17px;font-weight:400;text-transform:uppercase;letter-spacing:.5px}
.band-rule{display:flex;align-items:center;justify-content:center;gap:6px;margin:4px 0 14px}
.band-rule span{width:60px;height:1px;background:rgba(255,255,255,.7)}
.band-rule b{width:6px;height:6px;background:var(--white);transform:rotate(45deg)}
.project-grid{display:flex;justify-content:center;gap:18px}
.project{width:166px}
.project .photo{height:94px;border:3px solid var(--white)}
.project h3{font-size:10.5px;font-weight:900;text-transform:uppercase;margin:9px 0 3px;color:#1e1e1e}
.project a{color:var(--ink);font-size:8px;text-decoration:none}
.p1{background:linear-gradient(135deg,#7a6a55,#a78f70)}
.p2{background:linear-gradient(135deg,#5b4a3f,#9c7a61)}
.p3{background:linear-gradient(135deg,#2f6fb1,#8b6c4f)}

/* news & stories */
.updates{display:flex;justify-content:space-between;padding:16px 76px 0;height:180px}
.col{width:258px}
.news-item{display:flex;gap:8px;margin-bottom:10px}
.date{width:20px;height:20px;background:var(--blue);color:var(--white);font-size:7px;font-weight:700;text-align:center;line-height:20px;flex:none;border-radius:2px}
.news-item h4,.story h4{font-size:8.5px;font-weight:700}
.news-item p,.story p{color:var(--muted);font-size:7.5px;line-height:1.4}
.more{display:block;text-align:right;color:var(--orange);font-size:8px}
.story{display:flex;gap:9px}
.story .photo{width:72px;height:76px;flex:none;background:linear-gradient(140deg,#c7c2bb,#8e8a85)}

/* footer */
.site-footer{background:var(--footer);height:186px;color:#bdbdbd;display:flex;justify-content:space-between;padding:20px 76px 0}
.fcol h5{color:var(--white);font-size:9.5px;font-weight:700;text-transform:uppercase;display:flex;align-items:center;gap:6px;margin-bottom:10px}
.fcol h5::before{content:"";width:8px;height:8px;border-radius:50%;background:var(--orange)}
.links{list-style:none;font-size:7.5px;line-height:1.9;padding-left:14px}
.links li::before{content:"› ";color:var(--orange)}
.address{font-size:7.5px;line-height:1.6;width:150px}
.address .row{display:flex;align-items:center;gap:5px;margin-top:5px}
.address .dot{width:9px;height:9px;border-radius:50%;background:var(--orange);flex:none}
.fsocial{display:flex;gap:4px;margin-top:9px}
.fsocial span{width:13px;height:13px;border-radius:50%;background:#555;display:block}
.form{width:150px;font-size:7px}
.form label{display:flex;align-items:center;justify-content:space-between;margin-bottom:5px}
.form .field{width:112px;height:13px;background:var(--white)}
.form .field.tall{height:30px}
.form .submit{margin:4px 0 0 auto;width:40px;background:var(--orange);color:var(--white);font-weight:700;text-align:center;padding:3px 0;font-size:7px;text-transform:uppercase}
.copyright{background:var(--footer-deep);height:20px;color:#888;font-size:7px;text-align:center;line-height:20px}
</style>
</head>
<body>
<div class="page">

  <header class="site-header">
    <div class="topbar">
      <div class="phone">
        <svg width="9" height="9" viewBox="0 0 24 24"><path fill="#777" d="M6.6 10.8a15 15 0 0 0 6.6 6.6l2.2-2.2c.3-.3.7-.4 1-.2 1.1.4 2.3.6 3.6.6.6 0 1 .4 1 1V20c0 .6-.4 1-1 1A17 17 0 0 1 3 4c0-.6.4-1 1-1h3.5c.6 0 1 .4 1 1 0 1.3.2 2.5.6 3.6.1.3 0 .7-.2 1z"/></svg>
        Call +1 (555) 014 2290
      </div>
      <div class="social"><span class="s1"></span><span class="s2"></span><span class="s3"></span><span class="s4"></span></div>
    </div>
    <nav class="nav">
      <ul><li class="active">Home</li><li>About Marigold</li><li>Projects</li></ul>
      <ul><li>News/Stories</li><li>Giving</li><li>Contact</li></ul>
    </nav>
    <div class="brand"><span class="mark"></span><span class="name">MARIGOLD<br>VENTURE</span></div>
  </header>

  <section class="hero" role="img" aria-label="Group of smiling young women in pink shirts joining hands in a circle outdoors">
    <div class="hero-copy">
      <span class="line line-a">We Are Working In</span><br>
      <span class="line line-b">International Aid And Development</span><br>
      <span class="btn">Donate Now</span>
    </div>
  </section>

  <section class="welcome">
    <div class="welcome-text">
      <h2 class="section-title"><span class="title-icon"></span>Welcome to <em>Marigold</em></h2>
      <p class="lead">We walk beside local partners in Asia and Africa, backing projects that communities design and lead for themselves.</p>
      <p>Our partners are registered organisations rooted in the places they serve. Together we fund clean water, schooling, small farms and fair work, and we share the stories of the people behind every project so supporters can see where their giving goes and how it grows.</p>
      <span class="btn">Read More</span>
    </div>
    <div class="video" role="img" aria-label="Video still of many hands stacked together">
      <div class="video-bar">
        <svg width="7" height="7" viewBox="0 0 10 10"><path fill="#fff" d="M1 0l9 5-9 5z"/></svg>
        <div class="track"><i></i></div>
        <svg width="8" height="8" viewBox="0 0 10 10"><path fill="#fff" d="M0 3h3l3-3v10L3 7H0z"/></svg>
      </div>
    </div>
  </section>

  <section class="projects">
    <h2 class="band-title">Our Projects</h2>
    <div class="band-rule"><span></span><b></b><span></span></div>
    <div class="project-grid">
      <article class="project">
        <div class="photo p1" role="img" aria-label="Children sitting outside a village house in Cambodia"></div>
        <h3>Harvest Cambodia</h3><a>[ Read More ]</a>
      </article>
      <article class="project">
        <div class="photo p2" role="img" aria-label="Families gathered at a community meeting in Rwanda"></div>
        <h3>Hillside Rwanda</h3><a>[ Read More ]</a>
      </article>
      <article class="project">
        <div class="photo p3" role="img" aria-label="Volunteers beside a blue water building in Kenya"></div>
        <h3>Clearwater Kenya</h3><a>[ Read More ]</a>
      </article>
    </div>
  </section>

  <section class="updates">
    <div class="col">
      <h2 class="section-title"><span class="title-icon"></span>Latest <em>News</em></h2>
      <div class="news-item">
        <span class="date">12</span>
        <div><h4>New Well Opens</h4><p>A second village well now serves over two hundred families each day near the lake.</p></div>
      </div>
      <div class="news-item">
        <span class="date">04</span>
        <div><h4>School Term Begins</h4><p>Forty girls start classes this month thanks to our new bursary fund and partners.</p></div>
      </div>
      <span class="more">[ Read More ]</span>
    </div>
    <div class="col">
      <h2 class="section-title"><span class="title-icon"></span>Success <em>Stories</em></h2>
      <div class="story">
        <div class="photo" role="img" aria-label="Portrait of a project participant"></div>
        <div><p>Three years ago Amina sold vegetables from a mat by the road. With a small loan and training from our partner she now runs a stall, employs two neighbours and pays school fees for all four of her children. Her story shows what steady support can do when a community leads the way.</p></div>
      </div>
      <span class="more">[ Read More ]</span>
    </div>
  </section>

  <footer class="site-footer">
    <div class="fcol">
      <h5>Quick Links</h5>
      <ul class="links"><li>Home</li><li>About Marigold</li><li>Projects</li><li>News/Stories</li><li>Giving</li><li>Contact Us</li></ul>
    </div>
    <div class="fcol">
      <h5>Contact Address</h5>
      <div class="address">
        <strong style="color:#fff">Marigold</strong><br>
        27 Harbour Lane, Suite 4<br>Brookfield, NT 0800
        <div class="row"><span class="dot"></span>555-014-2290</div>
        <div class="row"><span class="dot"></span>hello@marigoldventure.org</div>
        <div class="fsocial"><span></span><span></span><span></span><span></span><span></span></div>
      </div>
    </div>
    <div class="fcol">
      <h5>Quick Contact</h5>
      <div class="form">
        <label>Name <span class="field"></span></label>
        <label>Email <span class="field"></span></label>
        <label>Message <span class="field tall"></span></label>
        <div class="submit">Submit</div>
      </div>
    </div>
  </footer>
  <div class="copyright">© 2024 Marigold. All Rights Reserved.</div>

</div>
</body>
</html>
```